Glimmora.ca Website Build For costume embellishment service

Design a website to promote our business.
Costume embellishing services for Artistic Swimming, Dance, Skating, Gymnastics etc.
We add sparkle to costumes using Kelvarne and Lumetta crystals to plain costumes that our customers provide. We also sell new costumes already decorated, Lastly we specialize in reimagining costumes to make them look like new.
We would like samples of our work to be displayed in pictures and video.
We need an information about our services page as well as a contact us page. We have a logo for Glimmora which is pink. We like a modern aesthetic as well as bright colours. We are hoping to promote our services worldwide but a big push for Canada. We need to convey that we are Canadian. We would like help with writing copy as well.
We currently have a cartwell webpage glimmora.ca but would like to shut down the cartwell site as we don't need the payment service. In the new website we will promote payment by PayRoam or transfer.
A copy of our logo is attached.

Target Market(s)

Athletes and Dancers under 18 years old and parents

Industry/Entity Type

costume embellishment service

Coding

Coded - Design and coding required

Number of Pages Required

4 page

Font styles to use
Sans Serif
Other font styles liked:
• match to the logo for titles

Colors
E54698
E96AAD
F1A4CE
F9D9EA
FCEFF6

Requirements
Must have
• Photos and video upload capability there will be allot of before and after pictures as well as unclose videos.
Nice to have
• modern look I like the look of this website http://www.bramblecloset-example.com
Should not have
• not busy looking

```html
<!DOCTYPE html>
<html lang="en">
<head>
<meta charset="utf-8">
<title>Glimmora – Costume Embellishment</title>
<link href="https://fonts.googleapis.com/css2?family=Kaushan+Script&family=Roboto:wght@400;500;700&display=swap" rel="stylesheet">
<style>
:root{
  --pink:#c42a8e;
  --pink-deep:#b21f80;
  --pale:#f6f6f6;
  --ink:#444;
  --white:#fff;
}
*{box-sizing:border-box;margin:0;padding:0}
html,body{width:1200px;height:3520px;overflow:hidden}
body{position:relative;background:var(--white);font-family:'Roboto',Arial,sans-serif;color:var(--ink)}
.abs{position:absolute}
.script{font-family:'Kaushan Script',cursive}
.btn{position:absolute;display:flex;align-items:center;justify-content:center;background:var(--pink);color:var(--white);border-radius:30px;font-family:'Kaushan Script',cursive;font-size:22px}
.divider{position:absolute;width:160px;height:4px;left:50%;transform:translateX(-50%);display:flex;justify-content:space-between}
.divider i{display:block;width:56px;height:2px;background:var(--pink)}
.divider.light i{background:var(--white)}
.photo{position:absolute}

.hero{position:absolute;left:0;top:0;width:1200px;height:580px;background:linear-gradient(180deg,#0c0c10 0%,#17161c 55%,#3a3a42 100%);overflow:hidden}
.hero-photo{left:600px;top:0;width:600px;height:580px;background:radial-gradient(ellipse at 55% 45%,#8a74c4 0%,#4a3f6a 30%,#221f2c 60%,rgba(20,20,26,0) 85%)}
.logo{position:absolute;display:flex;align-items:center;gap:10px;color:var(--white);font-weight:500}
.logo .dot{width:14px;height:14px;border-radius:50%;background:var(--white)}
.nav{position:absolute;top:40px;left:0;font-size:13px;font-weight:500;color:var(--white);text-transform:uppercase}
.nav span{position:absolute;white-space:nowrap}
.call{position:absolute;left:797px;top:27px;display:flex;gap:14px;align-items:center;color:var(--white)}
.call .circle{width:40px;height:40px;border-radius:50%;background:var(--pink);display:flex;align-items:center;justify-content:center}
.call small{display:block;font-size:11px}
.call strong{display:block;font-size:19px;font-weight:500}
.hero h1{position:absolute;left:128px;top:152px;width:450px;font-family:'Kaushan Script',cursive;font-weight:400;font-size:44px;line-height:63px;color:var(--white)}

.embellish{position:absolute;left:0;top:580px;width:1200px;height:514px;background:var(--pale)}
.embellish h2,.section-title{font-family:'Kaushan Script',cursive;font-weight:400;color:var(--pink);font-size:34px}
.embellish p{position:absolute;left:600px;top:180px;width:440px;font-size:13.5px;line-height:28px;color:var(--ink)}
.section-title{position:absolute;left:0;width:1200px;text-align:center}

.ba-band{position:absolute;left:0;top:2010px;width:1200px;height:343px;background:linear-gradient(120deg,var(--pink) 0%,#c93a97 50%,var(--pink-deep) 100%)}
.ba-card{position:absolute;left:131px;top:2195px;width:937px;height:508px;background:var(--white);box-shadow:0 4px 18px rgba(0,0,0,.18)}
.ba-frame{position:absolute;top:13px;width:445px;height:484px;border:1px solid #ddd}

.revive p{position:absolute;left:290px;top:2902px;width:620px;text-align:center;font-size:13.5px;line-height:28px}

footer{position:absolute;left:0;top:3126px;width:1200px;height:394px;background:linear-gradient(135deg,#c42a8e 0%,#b8248a 60%,#a91d7c 100%);color:var(--white)}
.f-nav{position:absolute;top:200px;left:0;width:1200px;font-size:13px;font-weight:500}
.f-nav span{position:absolute}
.contact{position:absolute;top:240px;display:flex;align-items:center;gap:14px}
.contact .circle{width:40px;height:40px;border-radius:50%;background:var(--white);display:flex;align-items:center;justify-content:center}
.contact small{display:block;font-size:11px}
.contact strong{display:block;font-size:17px;font-weight:400}
.contact strong.bold{font-weight:700}
.copy{position:absolute;top:334px;left:0;width:1200px;text-align:center;font-size:11px}
</style>
</head>
<body>

<header class="hero">
  <div class="photo hero-photo" role="img" aria-label="Figure skater in a sparkling violet costume leaping against blurred arena lights"></div>
  <div class="logo" style="left:132px;top:34px;font-size:30px"><span class="dot"></span>Glimmora</div>
  <nav class="nav">
    <span style="left:415px">Home</span>
    <span style="left:489px">About Us</span>
    <span style="left:590px">Gallery</span>
    <span style="left:683px">Contact Us</span>
  </nav>
  <div class="call">
    <div class="circle"><svg width="18" height="18" viewBox="0 0 24 24"><path fill="#fff" d="M6.6 10.8a15.1 15.1 0 0 0 6.6 6.6l2.2-2.2c.3-.3.7-.4 1-.2 1.1.4 2.3.6 3.6.6.6 0 1 .4 1 1V20c0 .6-.4 1-1 1A17 17 0 0 1 3 4c0-.6.4-1 1-1h3.5c.6 0 1 .4 1 1 0 1.3.2 2.5.6 3.6.1.3 0 .7-.2 1z"/></svg></div>
    <div><small>CALL US TODAY:</small><strong>+ 123 456 7890</strong></div>
  </div>
  <h1>Dazzling competition suits and costumes for all sports and events.</h1>
  <div class="btn" style="left:128px;top:364px;width:175px;height:53px">Get Started</div>
</header>

<section class="embellish">
  <div class="photo" style="left:180px;top:86px;width:348px;height:346px;background:linear-gradient(135deg,#e8b4d6,#b9789f 50%,#8a4c74)" role="img" aria-label="Costume designer sketching at a studio desk"></div>
  <h2 class="abs" style="left:600px;top:86px">Original Costume Embellishment</h2>
  <div class="divider" style="left:680px;top:150px"><i></i><i></i></div>
  <p>Our specialty is design and application, we do not alter the dimensions of the costume or provide any seamstress services.Provide the blank canvas (uniform/costume) and we work together on colours, patterns and design.We can personalize your swimsuit or costume, by adding Kelvarne or Lumetta rhinestones, sequins and embellishments. We can help create that WOW Factor!</p>
  <div class="btn" style="left:600px;top:365px;width:175px;height:54px">Learn More</div>
</section>

<section class="focus">
  <h2 class="section-title" style="top:1160px">Our Focus Area</h2>
  <div class="divider" style="top:1225px"><i></i><i></i></div>
  <div class="photo" style="left:130px;top:1260px;width:450px;height:328px;background:linear-gradient(135deg,#f0b540,#b6741e 55%,#3a2414)" role="img" aria-label="Carnival dancers in feathered headdresses and jewelled costumes"></div>
  <div class="photo" style="left:592px;top:1260px;width:256px;height:153px;background:linear-gradient(135deg,#c9b7a0,#8e2a2a 60%,#3d2a2a)" role="img" aria-label="Embroidered folk dance costume sleeves"></div>
  <div class="photo" style="left:592px;top:1427px;width:256px;height:161px;background:radial-gradient(circle at 55% 45%,#5a4a44,#1a1a1a 70%)" role="img" aria-label="Dancer in a beaded bra top on a dark background"></div>
  <div class="photo" style="left:860px;top:1260px;width:209px;height:328px;background:linear-gradient(160deg,#c9925a,#8a2a30 45%,#c2202a)" role="img" aria-label="Back of a red skating dress covered in crystals"></div>
  <div class="photo" style="left:130px;top:1601px;width:209px;height:328px;background:linear-gradient(135deg,#b7a9a0,#c23a3a 40%,#e8e2dc)" role="img" aria-label="Folk dancers in embroidered red and white costumes"></div>
  <div class="photo" style="left:351px;top:1601px;width:257px;height:153px;background:radial-gradient(circle at 40% 50%,#e6cfc6,#b38d82 70%)" role="img" aria-label="Close view of sequinned lace fabric"></div>
  <div class="photo" style="left:351px;top:1767px;width:257px;height:162px;background:linear-gradient(160deg,#6c7a70,#3f8a94 55%,#2c5f66)" role="img" aria-label="Swimmer in a patterned suit sitting by a pool"></div>
  <div class="photo" style="left:621px;top:1601px;width:448px;height:328px;background:linear-gradient(135deg,#cfcbc8,#9a9694 55%,#2c2c30)" role="img" aria-label="Black lace gown on a dress form"></div>
</section>

<section class="ba">
  <div class="ba-band"></div>
  <h2 class="section-title" style="top:2080px;color:var(--white)">Before / After</h2>
  <div class="divider light" style="top:2145px"><i></i><i></i></div>
  <div class="ba-card">
    <div class="ba-frame" style="left:19px;background:linear-gradient(180deg,#f0f0f0,#e6e6e6)" role="img" aria-label="Plain white gown on a dress form before embellishment"></div>
    <div class="ba-frame" style="left:475px;background:linear-gradient(180deg,#fafafa,#eeeeea)" role="img" aria-label="The same gown after lace and crystal embellishment"></div>
  </div>
  <div class="btn" style="left:273px;top:2603px;width:174px;height:52px">Before</div>
  <div class="btn" style="left:761px;top:2603px;width:174px;height:52px">After</div>
</section>

<section class="revive">
  <h2 class="section-title" style="top:2805px">Costume Revitalizing</h2>
  <div class="divider" style="top:2870px"><i></i><i></i></div>
  <p>Restyle or refresh an existing embellished costume by adding new stones to redesign the look.&nbsp; We can also replace missing stones and breathe new life tired or worn outfits.&nbsp; A great option for clubs to inexpensively rejuvenate existing inventory.</p>
  <div class="btn" style="left:513px;top:3000px;width:173px;height:53px">Learn More</div>
</section>

<footer>
  <div class="divider light" style="top:78px;width:224px"><i style="width:70px"></i><i style="width:70px"></i></div>
  <div class="logo" style="left:0;width:1200px;top:118px;justify-content:center;font-size:44px"><span class="dot"></span>Glimmora</div>
  <nav class="f-nav">
    <span style="left:425px">HOME</span>
    <span style="left:499px">ABOUT US</span>
    <span style="left:600px">GALLERY</span>
    <span style="left:693px">CONTACT US</span>
  </nav>
  <div class="contact" style="left:277px">
    <div class="circle"><svg width="18" height="14" viewBox="0 0 18 14"><rect x="0" y="0" width="18" height="14" rx="2" fill="#c42a8e"/><polyline points="1,1 9,8 17,1" stroke="#fff" stroke-width="1.6" fill="none"/></svg></div>
    <div><small>EMAIL ADDRESS</small><strong>info@glimmora.ca</strong></div>
  </div>
  <div class="contact" style="left:524px">
    <div class="circle"><svg width="18" height="18" viewBox="0 0 24 24"><path fill="#c42a8e" d="M6.6 10.8a15.1 15.1 0 0 0 6.6 6.6l2.2-2.2c.3-.3.7-.4 1-.2 1.1.4 2.3.6 3.6.6.6 0 1 .4 1 1V20c0 .6-.4 1-1 1A17 17 0 0 1 3 4c0-.6.4-1 1-1h3.5c.6 0 1 .4 1 1 0 1.3.2 2.5.6 3.6.1.3 0 .7-.2 1z"/></svg></div>
    <div><small>CALL US TODAY:</small><strong class="bold">+ 123 456 7890</strong></div>
  </div>
  <div class="contact" style="left:750px">
    <div class="circle"><svg width="18" height="18" viewBox="0 0 24 24"><path fill="#c42a8e" d="M6.6 10.8a15.1 15.1 0 0 0 6.6 6.6l2.2-2.2c.3-.3.7-.4 1-.2 1.1.4 2.3.6 3.6.6.6 0 1 .4 1 1V20c0 .6-.4 1-1 1A17 17 0 0 1 3 4c0-.6.4-1 1-1h3.5c.6 0 1 .4 1 1 0 1.3.2 2.5.6 3.6.1.3 0 .7-.2 1z"/></svg></div>
    <div><small>LOCATION</small><strong>123 Lorem ipsum dolor</strong></div>
  </div>
  <p class="copy">©Copyright 2021 <span class="script" style="font-size:17px">Glimmora</span> &nbsp;|&nbsp; All Rights Reserved</p>
</footer>

</body>
</html>
```